Games for Pupils Website Redesign

The purpose of the website redesign is to freshen up the content and update it to give a more modern look and feel. It will show what we do concisely and satisfy all potential visitors. We work with primary schools and the brand is fun.About: Games for Pupils is a scheme that brings top Olympic athletes into primary schools to inspire children to do more physical activity. We typically run a half day event at the school where the athlete does a fun fitness circuit with the children and then an inspirational assembly with a demonstration and Q&A. The children are asked to collect sponsorship money to take part in the event and a large proportion of the money raised goes back to the school in the form of a voucher for them to spend on new sports equipment. 1. To generate more leads from potential customers/schools2. To engage the children and parents more in the event and get them excited for their upcoming visit whilst setting up a fundraiser page.3. To simplify and modernise what is already there.

I have attached some ideas for each of the pages (uploaded in brief)

Here is a link to our current website: www.gamesforpupils.example

I have also attached a link to the sponsorship form which shows the kind of look and feel we're after.

Target Market(s)

Primary school teachers
Primary school parents

Number of Pages Required

5+ page

Requirements
Must have
• Fun, modern.
• Be built on kestrel framekit

```html
<!DOCTYPE html>
<html lang="en">
<head>
<meta charset="utf-8">
<title>Games for Pupils</title>
<link href="https://fonts.googleapis.com/css2?family=Mulish:wght@400;600;700&family=Open+Sans:wght@400&display=swap" rel="stylesheet">
<style>
  :root {
    --white: #ffffff;
    --ink: #222222;
    --navy: #1b2532;
    --hero-dark: #154f8a;
    --hero-mid: #1f6fbf;
    --hero-light: #2a86d6;
    --green: #60b535;
    --orange: #fe4e16;
    --stat-blue: #1a7fe6;
    --brand-red: #d4202f;
    --footer: #2a2a2a;
  }
  * { box-sizing: border-box; margin: 0; padding: 0; }
  html, body { width: 1200px; height: 982px; overflow: hidden; }
  body { font-family: "Mulish", sans-serif; color: var(--ink); background: var(--white); position: relative; }

  .site-header { position: absolute; top: 0; left: 0; width: 1200px; height: 98px; background: var(--white); }
  .brand { position: absolute; left: 144px; top: 30px; display: flex; align-items: center; gap: 10px; }
  .brand-mark { width: 34px; height: 34px; border-radius: 50%; background: var(--stat-blue); }
  .brand-name { font-weight: 700; font-size: 22px; color: var(--ink); letter-spacing: -0.2px; }
  .menu-toggle { position: absolute; left: 1011px; top: 27px; width: 44px; height: 44px; background: var(--navy); border-radius: 3px; display: flex; align-items: center; justify-content: center; }

  .hero { position: absolute; top: 98px; left: 0; width: 1200px; height: 516px;
    background: radial-gradient(ellipse at 55% 45%, var(--hero-light) 0%, var(--hero-mid) 45%, var(--hero-dark) 100%); }
  .hero-content { position: absolute; top: 54px; left: 144px; width: 912px; text-align: center; color: var(--white); }
  .hero-title { font-size: 34px; font-weight: 700; letter-spacing: 0.3px; line-height: 40px; }
  .hero-text { font-size: 16.5px; line-height: 25.6px; margin-top: 2px; }
  .hero-arrow { position: absolute; top: 340px; }
  .hero-arrow.prev { left: 46px; }
  .hero-arrow.next { left: 1132px; }

  .audience { position: absolute; top: 567px; width: 440px; height: 192px; border-radius: 3px; color: var(--white); text-align: center; }
  .audience.school { left: 144px; background: var(--green); }
  .audience.parent { left: 616px; background: var(--orange); }
  .audience-icon { position: absolute; top: 24px; left: 184px; }
  .audience-title { position: absolute; top: 98px; width: 100%; font-size: 26px; font-weight: 600; line-height: 32px; }
  .audience-text { position: absolute; top: 133px; width: 100%; font-family: "Open Sans", sans-serif; font-size: 13px; line-height: 19px; }

  .stats { position: absolute; top: 800px; left: 144px; width: 912px; display: flex; }
  .stat { flex: 1; text-align: center; }
  .stat-value { font-size: 40px; font-weight: 700; color: var(--stat-blue); line-height: 44px; }
  .stat-label { font-size: 13px; margin-top: 3px; }

  .site-footer { position: absolute; top: 902px; left: 0; width: 1200px; height: 80px; background: var(--footer); }
  .copyright { position: absolute; left: 145px; top: 31px; font-family: "Open Sans", sans-serif; font-size: 12px; color: var(--white); }
  .social { position: absolute; left: 771px; top: 27px; display: flex; gap: 7.4px; list-style: none; }
  .social li { width: 25px; height: 25px; border-radius: 50%; }
</style>
</head>
<body>
  <header class="site-header">
    <div class="brand">
      <span class="brand-mark"></span>
      <span class="brand-name">Games for Pupils</span>
    </div>
    <div class="menu-toggle" aria-label="Menu">
      <svg width="14" height="12" viewBox="0 0 14 12"><rect y="0" width="14" height="2.4" fill="#fff"/><rect y="4.8" width="14" height="2.4" fill="#fff"/><rect y="9.6" width="14" height="2.4" fill="#fff"/></svg>
    </div>
  </header>

  <section class="hero" role="img" aria-label="Photo of two smiling children with a blue tint">
    <div class="hero-content">
      <h1 class="hero-title">OUR MISSION</h1>
      <p class="hero-text">Phasellus nisl est, condimentum vitae faucibus in, sollicitudin vel metus. Nunc sit amet consequat risus. Curabitur ac elit leo. In eleifend dui tellus, in scelerisque elit porttitor et. Integer eu massa lacinia, lacinia nulla non, volutpat purus. Sed libero felis, vestibulum et dolor eget, lacinia aliquet neque.</p>
    </div>
    <svg class="hero-arrow prev" width="22" height="30" viewBox="0 0 22 30"><polyline points="16,3 5,15 16,27" fill="none" stroke="#fff" stroke-width="4"/></svg>
    <svg class="hero-arrow next" width="22" height="30" viewBox="0 0 22 30"><polyline points="6,3 17,15 6,27" fill="none" stroke="#fff" stroke-width="4"/></svg>
  </section>

  <article class="audience school">
    <svg class="audience-icon" width="72" height="52" viewBox="0 0 72 52" aria-hidden="true">
      <line x1="38" y1="2" x2="38" y2="14" stroke="#fff" stroke-width="1.5"/>
      <polygon points="38,2 45,4 38,7" fill="#fff"/>
      <polygon points="36,12 54,26 18,26" fill="#fff"/>
      <rect x="2" y="24" width="68" height="28" fill="#fff"/>
      <rect x="31" y="34" width="10" height="18" fill="#60b535"/>
      <rect x="8" y="32" width="14" height="12" fill="#60b535"/>
      <rect x="50" y="32" width="14" height="12" fill="#60b535"/>
    </svg>
    <h2 class="audience-title">I’M A SCHOOL</h2>
    <p class="audience-text">Aenean sed quam non sapien faucibus consequat vitae sit amet orci.<br>Praesent quis risus mi. In mollis nulla in pulvinar dictum.</p>
  </article>

  <article class="audience parent">
    <svg class="audience-icon" width="72" height="52" viewBox="0 0 72 52" aria-hidden="true">
      <circle cx="18" cy="9" r="6" fill="#fff"/>
      <rect x="10" y="18" width="16" height="34" rx="4" fill="#fff"/>
      <circle cx="56" cy="7" r="7" fill="#fff"/>
      <rect x="44" y="17" width="24" height="35" rx="4" fill="#fff"/>
      <circle cx="36" cy="28" r="5" fill="#fff" stroke="#fe4e16" stroke-width="2"/>
      <rect x="28" y="35" width="16" height="17" rx="4" fill="#fff" stroke="#fe4e16" stroke-width="2"/>
    </svg>
    <h2 class="audience-title">I’M A PARENT</h2>
    <p class="audience-text">Aenean sed quam non sapien faucibus consequat vitae sit amet orci.<br>Praesent quis risus mi. In mollis nulla in pulvinar dictum.</p>
  </article>

  <section class="stats">
    <div class="stat"><div class="stat-value">6254</div><div class="stat-label">Donec vestibulum odio</div></div>
    <div class="stat"><div class="stat-value">324</div><div class="stat-label">Aenean feugiat</div></div>
    <div class="stat"><div class="stat-value">82%</div><div class="stat-label">Donec sit amet</div></div>
    <div class="stat"><div class="stat-value">12</div><div class="stat-label">Proin porta</div></div>
    <div class="stat"><div class="stat-value">45158</div><div class="stat-label">Nullam accumsan</div></div>
    <div class="stat"><div class="stat-value">481</div><div class="stat-label">Praesent elementum</div></div>
  </section>

  <footer class="site-footer">
    <p class="copyright">Copyright &nbsp;©&nbsp; 2019 &nbsp;Games for Pupils. &nbsp;All rights reserved.</p>
    <ul class="social" aria-label="Social links">
      <li style="background:#3b5998"></li>
      <li style="background:#1d9ce5"></li>
      <li style="background:#0e76a8"></li>
      <li style="background:#dd4b39"></li>
      <li style="background:#cb2027"></li>
      <li style="background:#f57d00"></li>
      <li style="background:#e62117"></li>
      <li style="background:#4a7ba6"></li>
      <li style="background:#4caf50"></li>
    </ul>
  </footer>
</body>
</html>
```